Veltrane Group Business Card Design

The CEO is looking for a new trendy look for his business card.
You can stay with current branding or come up with something new/creative. It can be 3D, including Medical Office buildings. You can use our logo in a variety of colors. Please include name, title, company name, company website, email address, cell number

Target Market(s)

Real Estate Development and Construction

Industry/Entity Type

Health care real estate

Contact Information for Business Card

Rohesh Kamdar, CEO M-604.781.2249 E-roheshkamdar@veltrane.com Address:4180 Lindqvist Ave, Tampa, FL 33482 www.veltrane.com

Font styles to use
Other font styles liked:
• Be creative

Requirements
Must have
• Creative, trendy look
Nice to have
• Please go to our website to get a feel- www. veltrane.com
Should not have
• small fonts

```html
<!DOCTYPE html>
<html lang="en">
<head>
<meta charset="utf-8">
<title>Veltrane Group – Business Card</title>
<link rel="stylesheet" href="https://fonts.googleapis.com/css2?family=Poppins:wght@400;600;800&display=swap">
<style>
  :root {
    --brand-red: #b3202b;
    --brand-red-deep: #8c111a;
    --brand-navy: #1e3050;
    --paper-grey: #dcdcdc;
    --ink-white: #ffffff;
    --backdrop: #1b1b1b;
  }
  * { box-sizing: border-box; margin: 0; padding: 0; }
  html, body {
    width: 1200px; height: 900px; overflow: hidden;
    background: var(--backdrop);
    font-family: "Poppins", sans-serif;
  }
  .canvas {
    position: relative; width: 1200px; height: 900px;
  }
  .card {
    position: absolute; left: 250px; width: 700px; height: 400px;
    overflow: hidden;
    box-shadow: 0 12px 30px rgba(0,0,0,.55);
  }
  .card--front { top: 40px; background: var(--brand-red); }
  .card--back { top: 460px; background: var(--paper-grey); }

  .wordmark {
    position: absolute; font-weight: 800; line-height: 1; letter-spacing: -1px;
    white-space: nowrap;
  }
  .card--front .wordmark {
    left: 0; right: 0; top: 155px; text-align: center;
    font-size: 76px; color: var(--brand-red-deep);
  }
  .card--back .wordmark {
    left: 0; right: 0; top: 48px; text-align: center;
    font-size: 72px; color: var(--brand-red);
  }

  .band { position: absolute; left: 0; right: 0; }
  .band--red { top: 190px; height: 140px; background: var(--brand-red); }
  .band--navy { top: 330px; height: 70px; background: var(--brand-navy); }

  .person {
    position: absolute; right: 390px; top: 30px; text-align: right; color: var(--ink-white);
  }
  .person__name { font-weight: 600; font-size: 24px; letter-spacing: .5px; text-transform: uppercase; }
  .person__title { font-weight: 400; font-size: 19px; margin-top: 2px; }

  .divider {
    position: absolute; left: 340px; top: 22px; width: 2px; height: 96px; background: var(--ink-white);
  }

  .contacts { position: absolute; left: 365px; top: 22px; list-style: none; color: var(--ink-white); }
  .contacts li {
    display: flex; align-items: center; gap: 10px;
    font-size: 18px; line-height: 32px;
  }
  .contacts svg { width: 18px; height: 18px; flex: none; fill: var(--ink-white); }

  .address {
    position: absolute; left: 0; right: 0; top: 20px; text-align: center;
    color: var(--ink-white); font-size: 20px;
  }
</style>
</head>
<body>
<main class="canvas">
  <section class="card card--front" aria-label="Card front">
    <p class="wordmark">Veltrane Group</p>
  </section>

  <section class="card card--back" aria-label="Card back">
    <p class="wordmark">Veltrane Group</p>

    <div class="band band--red">
      <div class="person">
        <p class="person__name">Rohesh Kamdar</p>
        <p class="person__title">CEO</p>
      </div>
      <span class="divider"></span>
      <ul class="contacts">
        <li>
          <svg viewBox="0 0 24 24" aria-hidden="true"><path d="M6.6 10.8a15.1 15.1 0 0 0 6.6 6.6l2.2-2.2a1 1 0 0 1 1-.25 11.4 11.4 0 0 0 3.6.57 1 1 0 0 1 1 1V20a1 1 0 0 1-1 1A17 17 0 0 1 3 4a1 1 0 0 1 1-1h3.5a1 1 0 0 1 1 1c0 1.25.2 2.45.57 3.6a1 1 0 0 1-.25 1z"/></svg>
          604.781.2249
        </li>
        <li>
          <svg viewBox="0 0 24 24" aria-hidden="true"><path d="M2 5h20v14H2zm2 2v.5l8 5 8-5V7zm0 2.9V17h16V9.9l-8 5z"/></svg>
          roheshkamdar@veltrane.com
        </li>
        <li>
          <svg viewBox="0 0 24 24" aria-hidden="true"><path d="M12 2a10 10 0 1 0 0 20 10 10 0 0 0 0-20zm6.9 6h-3a15 15 0 0 0-1.3-3.9A8 8 0 0 1 18.9 8zM12 4c.9 1.2 1.6 2.6 2 4h-4c.4-1.4 1.1-2.8 2-4zM4.3 14a8 8 0 0 1 0-4h3.4a16 16 0 0 0 0 4zm.8 2h3a15 15 0 0 0 1.3 3.9A8 8 0 0 1 5.1 16zM8 8H5.1a8 8 0 0 1 4.3-3.9A15 15 0 0 0 8 8zm4 12c-.9-1.2-1.6-2.6-2-4h4c-.4 1.4-1.1 2.8-2 4zm2.3-6H9.7a14 14 0 0 1 0-4h4.6a14 14 0 0 1 0 4zm.3 5.9a15 15 0 0 0 1.3-3.9h3a8 8 0 0 1-4.3 3.9zm1.7-5.9a16 16 0 0 0 0-4h3.4a8 8 0 0 1 0 4z"/></svg>
          www.veltrane.com
        </li>
      </ul>
    </div>

    <div class="band band--navy">
      <p class="address">4180 Lindqvist Ave, Tampa, FL 33482</p>
    </div>
  </section>
</main>
</body>
</html>
```